Dusty Spur Outfitters Home Page

I need a logo and page design for my home page, maybe some background color suggestions to go with it. I want the logo to project "vintage" and "western wear" but not be your typical trite western saddle and gun type thing.
http://www.dustyspuroutfitters.example/store/cart.php
Not looking for page coding just logo and other design elements to lay in over the site's template to make it "pop"
Reason: Have to finalize the design.
Target Market(s)
My customers are 70/30 men to women.
Industry/Entity Type
Gun

```html
<!DOCTYPE html>
<html lang="en">
<head>
<meta charset="utf-8">
<title>Dusty Spur Outfitters – Header Variations</title>
<link href="https://fonts.googleapis.com/css2?family=Lato:wght@700;900&family=Kaushan+Script&display=swap" rel="stylesheet">
<style>
  :root {
    --canvas-sand: #d7c5a5;
    --band-teal: #3a9fb0;
    --band-teal-dark: #2d8797;
    --panel-charcoal: #262626;
    --panel-shade: #1c1c1c;
    --cream: #e8dcc2;
    --ink: #2e2a26;
    --gold: #f0c158;
    --accent-red: #d9452a;
    --accent-teal: #69b3c4;
    --accent-gold: #f2c95c;
  }
  * { margin: 0; padding: 0; box-sizing: border-box; }
  html, body { width: 1200px; height: 1000px; overflow: hidden; }
  body {
    background: var(--canvas-sand);
    position: relative;
    font-family: "Lato", Arial, sans-serif;
  }
  .header-variant {
    position: absolute;
    left: 0;
    width: 1200px;
    height: 168px;
    background: var(--band-teal);
    box-shadow: 0 2px 3px rgba(0,0,0,0.25);
  }
  .header-variant--one { top: 73px; }
  .header-variant--two { top: 298px; }
  .header-variant--three { top: 533px; }
  .header-variant--four { top: 762px; }

  .header-panel {
    position: absolute;
    left: 0; right: 0;
    top: 20px;
    height: 124px;
    background: linear-gradient(180deg, var(--panel-shade), var(--panel-charcoal) 30%, var(--panel-charcoal) 70%, var(--panel-shade));
  }
  .brand {
    position: absolute;
    left: 70px;
    top: 0;
    height: 168px;
    width: 390px;
    display: flex;
    align-items: center;
    gap: 12px;
  }
  .brand-dot {
    width: 22px; height: 22px;
    border-radius: 50%;
    flex: none;
  }
  .header-variant--one .brand-dot { background: var(--accent-red); }
  .header-variant--two .brand-dot,
  .header-variant--three .brand-dot { background: var(--accent-teal); }
  .header-variant--four .brand-dot { background: var(--accent-gold); }
  .brand-name {
    font-weight: 900;
    font-size: 31px;
    letter-spacing: 0.5px;
    color: var(--gold);
    white-space: nowrap;
  }
  .tagline {
    position: absolute;
    left: 476px;
    top: 88px;
    font-family: "Kaushan Script", cursive;
    font-size: 22px;
    color: var(--cream);
    white-space: nowrap;
  }
  .search {
    position: absolute;
    left: 901px;
    top: 52px;
    display: flex;
    align-items: center;
    gap: 11px;
  }
  .search-field {
    width: 172px;
    height: 30px;
    border-radius: 15px;
    background: var(--cream);
    color: var(--ink);
    font-weight: 700;
    font-size: 17px;
    line-height: 30px;
    padding-left: 17px;
  }
  .search-go {
    font-weight: 700;
    font-size: 18px;
    color: var(--cream);
  }
</style>
</head>
<body>

<header class="header-variant header-variant--one">
  <div class="header-panel"></div>
  <div class="brand"><span class="brand-dot"></span><span class="brand-name">Dusty Spur Outfitters</span></div>
  <p class="tagline">Brand-New Retro Styled Western Wear</p>
  <div class="search"><span class="search-field">Search...</span><span class="search-go">GO!</span></div>
</header>

<header class="header-variant header-variant--two">
  <div class="header-panel"></div>
  <div class="brand"><span class="brand-dot"></span><span class="brand-name">Dusty Spur Outfitters</span></div>
  <p class="tagline">Brand-New Retro Styled Western Wear</p>
  <div class="search"><span class="search-field">Search...</span><span class="search-go">GO!</span></div>
</header>

<header class="header-variant header-variant--three">
  <div class="header-panel"></div>
  <div class="brand"><span class="brand-dot"></span><span class="brand-name">Dusty Spur Outfitters</span></div>
  <p class="tagline">Brand-New Retro Styled Western Wear</p>
  <div class="search"><span class="search-field">Search...</span><span class="search-go">GO!</span></div>
</header>

<header class="header-variant header-variant--four">
  <div class="header-panel"></div>
  <div class="brand"><span class="brand-dot"></span><span class="brand-name">Dusty Spur Outfitters</span></div>
  <p class="tagline">Brand-New Retro Styled Western Wear</p>
  <div class="search"><span class="search-field">Search...</span><span class="search-go">GO!</span></div>
</header>

</body>
</html>
```